Website for IT consulting Company

I need a website upgrade, the existing site content is ok, I would also like to add a testimonial page, the site should be something that is easy for us to update content. You use the content from www.kelvanbrook.com as an example. I will also post update logo and artwork. I also need a contact form with some type of validation or captcha.

I added Coded to the Project

Please omit Address maps

Target Market(s)

small business, service oriented companies. We provide IT Consulting, support and mangement

Industry/Entity Type

Information Technology

Coding

Number of Pages Required

1 page

Font styles to use
Serif
Sans Serif

Requirements
Must have
• Contain logo attached, and content from existing web site www.kelvanbrook.com.
• Also need to update content easily, and be movable to different platforms.
• There is a catch phrase
• "Let us worry about your technology…” “ so you don’t have to!”
• Should be included.
Nice to have
• Testimonial page, Project page where we can post new and past projects and pictures
Should not have
• none

```html
<!DOCTYPE html>
<html lang="en">
<head>
<meta charset="utf-8">
<title>Kelvanbrook – IT solutions that work for your business</title>
<link href="https://fonts.googleapis.com/css2?family=Lato:wght@400;700&family=Open+Sans:ital,wght@0,400;0,600;0,700;1,400&display=swap" rel="stylesheet">
<style>
:root{
  --orange:#f07a26;
  --orange-dark:#e36b17;
  --blue:#2a86cf;
  --blue-deep:#1f6fb4;
  --ink:#333333;
  --muted:#555555;
  --grey:#5a5a5a;
  --cream:#faf6f1;
  --line:#e2e2e2;
  --white:#ffffff;
}
*{box-sizing:border-box;margin:0;padding:0}
html,body{width:1200px;height:3114px;overflow:hidden}
body{position:relative;background:var(--white);font-family:"Open Sans",Arial,sans-serif;color:var(--ink)}
a{color:inherit;text-decoration:none}

/* header */
.site-header{position:absolute;left:0;top:0;width:1200px;height:112px;background:var(--white)}
.brand{position:absolute;left:97px;top:30px;display:flex;align-items:center;gap:12px}
.brand-mark{width:38px;height:38px;background:var(--orange)}
.brand-name{font-family:"Lato",sans-serif;font-weight:700;font-size:30px;color:var(--grey);letter-spacing:1px}
.top-contact{position:absolute;top:20px;right:90px;display:flex;gap:22px;font-size:16px;font-weight:600}
.top-contact span{display:flex;align-items:center;gap:8px}
.top-contact .mail{color:var(--orange)}
.top-contact .phone{color:var(--blue-deep)}
.dot-icon{width:28px;height:28px;border-radius:50%;display:inline-flex;align-items:center;justify-content:center}
.main-nav{position:absolute;top:72px;right:90px;display:flex;gap:37px;font-size:14px;font-weight:600;color:var(--ink)}
.main-nav .active{color:var(--orange)}

/* hero */
.hero{position:absolute;left:0;top:112px;width:1200px;height:514px;background:linear-gradient(100deg,#7d8a96 0%,#a9b2b9 35%,#54606b 65%,#2d3640 100%)}
.hero-title{position:absolute;left:97px;top:105px;font-family:"Lato",sans-serif;font-weight:700;font-size:58px;color:var(--white);letter-spacing:1px}
.hero-sub{position:absolute;left:97px;top:196px;font-size:19px;line-height:32px;color:var(--white)}
.hero-btn{position:absolute;left:97px;top:286px;width:118px;height:48px;border:2px solid var(--white);color:var(--white);font-size:15px;font-weight:600;display:flex;align-items:center;justify-content:center}
.hero-dots{position:absolute;left:97px;top:370px;display:flex;gap:5px}
.hero-dots i{width:13px;height:13px;border-radius:50%;border:2px solid var(--white)}
.hero-dots i.on{border-color:var(--orange);background:var(--white)}
.hero-notch{position:absolute;left:560px;top:474px}

/* welcome */
.section-title{position:absolute;left:0;width:1200px;text-align:center;font-family:"Lato",sans-serif;font-weight:700;font-size:28px;color:var(--orange)}
.welcome-intro{position:absolute;left:150px;top:746px;width:900px;text-align:center;font-size:14px;line-height:26px;color:var(--muted)}
.service{position:absolute;top:830px;width:260px;text-align:center}
.service-circle{width:174px;height:174px;border-radius:50%;margin:0 auto;display:flex;align-items:center;justify-content:center;border:4px solid var(--orange);padding:6px}
.service-circle .fill{width:100%;height:100%;border-radius:50%;background:var(--orange);display:flex;align-items:center;justify-content:center}
.service.dark .service-circle{border-color:var(--grey)}
.service.dark .service-circle .fill{background:var(--grey)}
.service h3{margin-top:46px;font-size:15px;font-weight:700;color:var(--orange);text-transform:uppercase}
.service.dark h3{color:var(--ink)}
.service p{margin-top:12px;font-size:12.5px;line-height:21px;color:var(--ink)}
.pill{display:inline-block;margin-top:22px;width:100px;height:36px;line-height:36px;border-radius:18px;background:var(--orange);color:var(--white);font-size:13px;font-weight:600}
.service.dark .pill{background:var(--grey)}

/* features */
.features{position:absolute;left:0;top:1282px;width:1200px;height:546px;background:linear-gradient(180deg,var(--blue) 0%,var(--blue-deep) 100%)}
.features-notch{position:absolute;left:530px;top:0}
.features h2{position:absolute;left:0;top:92px;width:1200px;text-align:center;font-family:"Lato",sans-serif;font-weight:700;font-size:27px;color:var(--white)}
.features .rule{position:absolute;left:515px;top:144px;width:170px;height:2px;background:var(--white)}
.feature{position:absolute;width:330px;display:flex;gap:18px;color:var(--white)}
.feature svg{flex:none;margin-top:2px}
.feature h4{font-size:20px;font-weight:400;margin-bottom:8px}
.feature p{font-size:12.5px;line-height:20px;text-align:justify;width:256px;opacity:.95}

/* about */
.about-title{position:absolute;left:97px;top:1874px;font-family:"Lato",sans-serif;font-weight:700;font-size:27px;color:var(--orange)}
.about-text{position:absolute;left:97px;top:1946px;width:620px;font-size:13.5px;line-height:24px;color:var(--ink)}
.about-text p+p{margin-top:10px}
.about-btn{position:absolute;left:97px;top:2162px;width:118px;height:48px;background:var(--orange);color:var(--white);font-size:15px;font-weight:600;display:flex;align-items:center;justify-content:center}
.about-visual{position:absolute;left:752px;top:1880px;width:448px;height:352px;background:linear-gradient(135deg,#eceae7 0%,#d8d4cf 55%,#e9c9a8 100%)}

/* testimonials */
.testimonials{position:absolute;left:0;top:2260px;width:1200px;height:490px;background:var(--cream)}
.testimonials .rule{position:absolute;left:550px;top:104px;width:100px;height:2px;background:var(--orange)}
.quote{position:absolute;top:156px;width:296px;height:176px;background:var(--white);border:1px solid var(--line);padding:26px 20px 0 54px;font-style:italic;font-size:12.5px;line-height:24px;color:var(--muted)}
.quote::before{content:"\201C";position:absolute;left:16px;top:4px;font-size:44px;font-style:normal;font-weight:700;color:var(--orange)}
.quote::after{content:"";position:absolute;left:18px;bottom:-16px;border-left:16px solid var(--white);border-bottom:16px solid transparent}
.quote.featured{background:var(--orange);color:var(--white);border-color:var(--orange)}
.quote.featured::before{color:var(--white)}
.quote.featured::after{border-left-color:var(--orange)}
.author{position:absolute;top:360px;display:flex;align-items:center;gap:16px}
.avatar{width:60px;height:60px;border-radius:50%;background:linear-gradient(135deg,#c9b3a3,#6e5a4f);border:3px solid var(--white);box-shadow:0 0 0 1px var(--line)}
.author b{display:block;font-size:15px;font-weight:600;color:var(--ink)}
.author span{font-size:13.5px;color:var(--muted)}

/* footer */
.site-footer{position:absolute;left:0;top:2750px;width:1200px;height:364px}
.footer-brand{position:absolute;left:0;top:60px;width:1200px;display:flex;justify-content:center;align-items:center;gap:12px}
.footer-contact{position:absolute;left:0;top:156px;width:1200px;display:flex;justify-content:center;gap:26px;font-size:18px;color:var(--ink)}
.footer-contact span{display:flex;align-items:center;gap:10px}
.ring{width:34px;height:34px;border:2px solid var(--ink);border-radius:50%;display:inline-flex;align-items:center;justify-content:center}
.footer-nav{position:absolute;left:0;top:232px;width:1200px;display:flex;justify-content:center;gap:28px;font-size:14px;font-weight:600;color:var(--ink)}
.footer-rule{position:absolute;left:97px;top:290px;width:1013px;height:1px;background:var(--ink)}
.copyright{position:absolute;left:97px;top:318px;font-size:13.5px;color:var(--ink)}
.socials{position:absolute;left:906px;top:310px;display:flex;gap:8px}
.socials i{width:32px;height:32px;border-radius:50%;border:2px solid var(--ink)}
</style>
</head>
<body>

<header class="site-header">
  <div class="brand"><span class="brand-mark"></span><span class="brand-name">KELVANBROOK</span></div>
  <div class="top-contact">
    <span class="mail"><i class="dot-icon" style="background:var(--orange)"><svg width="14" height="10" viewBox="0 0 14 10"><rect x="0.5" y="0.5" width="13" height="9" fill="none" stroke="#fff"/><path d="M1 1l6 5 6-5" fill="none" stroke="#fff"/></svg></i>info@kelvanbrook.com</span>
    <span class="phone"><i class="dot-icon" style="background:var(--blue-deep)"><svg width="12" height="14" viewBox="0 0 12 14"><path d="M2 1l3 0 1 3-2 1c1 2 2 3 4 4l1-2 3 1v3c-6 1-11-4-10-10z" fill="#fff"/></svg></i>180 555 0192</span>
  </div>
  <nav class="main-nav">
    <a class="active">HOME</a><a>ABOUT</a><a>SUPPORT</a><a>CLIENTS</a><a>CAREERS</a><a>CONTACT</a>
  </nav>
</header>

<section class="hero" role="img" aria-label="Photo of two businessmen in suits reviewing a tablet together">
  <h1 class="hero-title">KELVANBROOK</h1>
  <p class="hero-sub">IT solutions that work for your business<br>A full service technology company</p>
  <a class="hero-btn">Read More</a>
  <div class="hero-dots"><i class="on"></i><i></i><i></i><i></i><i></i></div>
  <svg class="hero-notch" width="80" height="40" viewBox="0 0 80 40"><polygon points="0,40 40,0 80,40" fill="#fff"/></svg>
</section>

<h2 class="section-title" style="top:690px">WELCOME TO KELVANBROOK</h2>
<p class="welcome-intro">Outsourcing is subcontracting a process, such as product design or manufacturing, to a third-party company. The decision to outsource is often made in the interest of lowering firm costs, redirecting or conserving energy.</p>

<div class="service" style="left:46px">
  <div class="service-circle"><div class="fill"><svg width="70" height="60" viewBox="0 0 70 60" fill="none" stroke="#fff" stroke-width="3"><rect x="12" y="4" width="52" height="36"/><polyline points="20,32 32,20 40,26 54,12"/><path d="M4 56l10-16 8 4"/></svg></div></div>
  <h3>Managed IT Solutions</h3>
  <p>Our staff will design, service, administer and maintain your IT needs. We are well versed on all major operating system.</p>
  <span class="pill">MORE</span>
</div>
<div class="service dark" style="left:318px">
  <div class="service-circle"><div class="fill"><svg width="64" height="64" viewBox="0 0 64 64" fill="none" stroke="#fff" stroke-width="3"><rect x="24" y="6" width="32" height="44"/><line x1="32" y1="16" x2="48" y2="16"/><line x1="32" y1="24" x2="48" y2="24"/><circle cx="22" cy="40" r="10"/><line x1="15" y1="47" x2="6" y2="58"/></svg></div></div>
  <h3>Remote Diagnostic</h3>
  <p>Our staff will design, service, administer and maintain your IT needs. We are well versed on all major operating system.</p>
  <span class="pill">MORE</span>
</div>
<div class="service" style="left:605px">
  <div class="service-circle"><div class="fill"><svg width="70" height="64" viewBox="0 0 70 64" fill="none" stroke="#fff" stroke-width="3"><path d="M35 4l16 6v10c0 10-8 16-16 18-8-2-16-8-16-18V10z"/><polyline points="28,20 33,25 42,15"/><circle cx="14" cy="46" r="5"/><circle cx="35" cy="46" r="5"/><circle cx="56" cy="46" r="5"/><path d="M4 62c0-6 20-6 20 0M25 62c0-6 20-6 20 0M46 62c0-6 20-6 20 0"/></svg></div></div>
  <h3>IT Infrastructure Design</h3>
  <p>Our staff will design, service, administer and maintain your IT needs. We are well versed on all major operating system.</p>
  <span class="pill">MORE</span>
</div>
<div class="service" style="left:878px">
  <div class="service-circle"><div class="fill"><svg width="70" height="64" viewBox="0 0 70 64" fill="#fff"><rect x="24" y="4" width="22" height="22" rx="4"/><rect x="20" y="28" width="30" height="6"/><rect x="4" y="36" width="62" height="6"/><rect x="10" y="42" width="5" height="18"/><rect x="55" y="42" width="5" height="18"/></svg></div></div>
  <h3>Design and Installation</h3>
  <p>Our staff will design, service, administer and maintain your IT needs. We are well versed on all major operating system.</p>
  <span class="pill">MORE</span>
</div>

<section class="features">
  <svg class="features-notch" width="140" height="44" viewBox="0 0 140 44"><polygon points="0,0 140,0 70,44" fill="#fff"/></svg>
  <h2>MAJOR ACCOUNTS SALES EXECUTIVE</h2>
  <div class="rule"></div>

  <div class="feature" style="left:95px;top:216px"><svg width="40" height="40" viewBox="0 0 40 40" fill="none" stroke="#fff" stroke-width="2.5"><rect x="12" y="3" width="24" height="18" rx="3"/><circle cx="14" cy="28" r="9"/><text x="10" y="33" fill="#fff" stroke="none" font-size="13" font-weight="700">$</text></svg><div><h4>Technology Sales</h4><p>Technology solution provider based in Houston, Texas. Our goal is to make tech nology a non-issue for individuals.</p></div></div>
  <div class="feature" style="left:445px;top:216px"><svg width="40" height="40" viewBox="0 0 40 40" fill="#fff"><circle cx="20" cy="8" r="6"/><path d="M10 26c0-8 20-8 20 0z"/><rect x="4" y="30" width="32" height="4"/></svg><div><h4>Working Knowledge</h4><p>Technology solution provider based in Houston, Texas. Our goal is to make tech nology a non-issue for individuals.</p></div></div>
  <div class="feature" style="left:800px;top:216px"><svg width="40" height="40" viewBox="0 0 40 40" fill="#fff"><circle cx="20" cy="6" r="4"/><rect x="17" y="12" width="6" height="8"/><circle cx="7" cy="26" r="4"/><circle cx="33" cy="26" r="4"/><rect x="2" y="32" width="10" height="6"/><rect x="28" y="32" width="10" height="6"/><rect x="8" y="20" width="24" height="2"/></svg><div><h4>IT Service and support</h4><p>Technology solution provider based in Houston, Texas. Our goal is to make tech nology a non-issue for individuals.</p></div></div>
  <div class="feature" style="left:95px;top:370px"><svg width="40" height="40" viewBox="0 0 40 40" fill="#fff"><path d="M4 10l24-6 4 22-24 6z"/><rect x="10" y="28" width="20" height="4" fill="#2a86cf"/></svg><div><h4>Managing database</h4><p>Technology solution provider based in Houston, Texas. Our goal is to make tech nology a non-issue for individuals.</p></div></div>
  <div class="feature" style="left:445px;top:370px"><svg width="40" height="40" viewBox="0 0 40 40" fill="#fff"><rect x="2" y="4" width="36" height="24" rx="2"/><rect x="16" y="28" width="8" height="6"/><rect x="10" y="34" width="20" height="3"/></svg><div><h4>Sales and collections</h4><p>Technology solution provider based in Houston, Texas. Our goal is to make tech nology a non-issue for individuals.</p></div></div>
  <div class="feature" style="left:800px;top:370px"><svg width="40" height="40" viewBox="0 0 40 40" fill="#fff"><circle cx="10" cy="8" r="5"/><rect x="5" y="15" width="10" height="22"/><rect x="20" y="6" width="16" height="5"/><rect x="20" y="16" width="16" height="5"/><rect x="20" y="26" width="16" height="5"/></svg><div><h4>Kelvanbrook Development</h4><p>Technology solution provider based in Houston, Texas. Our goal is to make tech nology a non-issue for individuals.</p></div></div>
</section>

<h2 class="about-title">KELVANBROOK DEVELOPMENT GROUP</h2>
<div class="about-text">
  <p>Kelvanbrook Development Group, Inc. was established in 1991. Our mission is helping businesses and individuals realize a Return on Investment by implementing today's advanced technologies. As a small business we understand the importance of technology and personalized attention. Every member of our support team has worked with both large and small companies supporting a multitude of applications, networks and environments.</p>
  <p>We interface daily with Clients and their customers to establish your support needs. A prerequisite for working with Kelvanbrook is having both the technological knowledge and the customer skills to communicate and work with customers to resolve technology issues.</p>
</div>
<a class="about-btn">Read More</a>
<div class="about-visual" role="img" aria-label="Illustration of a hand holding a tablet that shows the company name"></div>

<section class="testimonials">
  <h2 class="section-title" style="top:58px">CLIENT TESTIMONIALS</h2>
  <div class="rule"></div>

  <blockquote class="quote" style="left:102px">Duis aute irure dolor in reprehen derit in voluptate velit esse cillum dolore eu fugiat nulla pariatur. Ex cepteur sint occaecat cupidatat non proident.</blockquote>
  <blockquote class="quote featured" style="left:452px">Duis aute irure dolor in reprehen derit in voluptate velit esse cillum dolore eu fugiat nulla pariatur. Ex cepteur sint occaecat cupidatat non proident.</blockquote>
  <blockquote class="quote" style="left:804px">Duis aute irure dolor in reprehen derit in voluptate velit esse cillum dolore eu fugiat nulla pariatur. Ex cepteur sint occaecat cupidatat non proident.</blockquote>

  <div class="author" style="left:98px"><div class="avatar" role="img" aria-label="Client portrait"></div><div><b>Easy and Convenient</b><span>Perspiciatis</span></div></div>
  <div class="author" style="left:450px"><div class="avatar" role="img" aria-label="Client portrait"></div><div><b>Good /And Effective Work</b><span>Perspiciatis</span></div></div>
  <div class="author" style="left:802px"><div class="avatar" role="img" aria-label="Client portrait"></div><div><b>Easy and Convenient</b><span>Perspiciatis</span></div></div>
</section>

<footer class="site-footer">
  <div class="footer-brand"><span class="brand-mark"></span><span class="brand-name">KELVANBROOK</span></div>
  <div class="footer-contact">
    <span><i class="ring"><svg width="16" height="12" viewBox="0 0 16 12"><rect x="1" y="1" width="14" height="10" fill="none" stroke="#333" stroke-width="1.5"/><path d="M1 1l7 6 7-6" fill="none" stroke="#333" stroke-width="1.5"/></svg></i>info@kelvanbrook.com</span>
    <span><i class="ring"><svg width="14" height="16" viewBox="0 0 12 14"><path d="M2 1l3 0 1 3-2 1c1 2 2 3 4 4l1-2 3 1v3c-6 1-11-4-10-10z" fill="#333"/></svg></i>180 555 0192</span>
  </div>
  <nav class="footer-nav">
    <a>HOME</a><span>|</span><a>ABOUT US</a><span>|</span><a>SUPPORT</a><span>|</span><a>CLIENTS</a><span>|</span><a>CAREERS</a><span>|</span><a>CONTACT</a>
  </nav>
  <div class="footer-rule"></div>
  <p class="copyright">Copyright © 2017 Kelvanbrook. All Right Reserved</p>
  <div class="socials" aria-label="Social links"><i></i><i></i><i></i><i></i><i></i></div>
</footer>

</body>
</html>
```